Window Treatment business needs website redesigned.

We need a revamp and refresh of our current site www.velmarix.ca
Looking to attract very high end customer. It should be a very simple design with very little text. This site will be visited by prospective homeowners, designers, builders and architects. They should feel that they are dealing with a high-end product selection, where experience, customer service and unique product offering is the focus. The content will be to highlight our services and highlight the manufacturers we sell, using a few rich photos to highlight the products. We should NOT look like we are a very large company. It should NOT have discounts/savings buttons and many menus to choose from. We offer over 15 years experience to narrow the many market options, to provide the right technical solution.
We specialize in products that are not readily available on the market and specifically motorized systems for indoors and outdoors.
Our main suppliers are Kravenholt.com, Dimbrell.com
We carry our own locally manufactured product line of roller shades.
Main product pictures should be of roller shades, outdoor bug screens, awnings and outdoor pergolas.

Reason: I understand that Christmas is coming up real short and many people are extremely busy. If you have a CREATIVE gifting you still want to submit, I look forward to your idea!

Reason: Due to holiday season, we have not had sufficient time to review to make a final decision. Thank you for your patience!

Target Market(s)

High end home owners, designers, builders, architects

Industry/Entity Type

Contractor

Coding

Coded - Design and coding required

Number of Pages Required

3 page

Font styles to use
Sans Serif

Requirements
Must have
• Landing page with full size image like homepage of zolvane.it
• Products page that highlights products with simple product shot image, description and link to manufacturer.
• On main page a scrolling of customer reviews.
• I want a very simple, eye-catching, emotional image for homepage. It does not need to include any product image.
• An image that shows technology combining/meshing with hand craftsmanship.
• Focus is on design.
• http://www.zolvane.it/en/gallery is a great layout and design.
Nice to have
• Logo shape for icons and watermark should be used.
• Look like and have simple motion effects like quorix.com or telvarin.com
Should not have
• Generic/standard looking feel like bluppet.com or mecklorwindow.ca
• No use of green as background only subtle text.
• Lots of text and pages.

```html
<!DOCTYPE html>
<html lang="en">
<head>
<meta charset="utf-8">
<title>Velmarix Window Treatment Solutions</title>
<link href="https://fonts.googleapis.com/css2?family=Raleway:wght@400;500;600;700&family=Arimo:wght@400;700&display=swap" rel="stylesheet">
<style>
:root{
  --green:#6cc04a;
  --ink:#1b1b1b;
  --black:#141414;
  --charcoal:#262826;
  --grey-bg:#ececec;
  --text:#6b6b6b;
  --white:#ffffff;
  --line:#d6d6d6;
}
*{box-sizing:border-box;margin:0;padding:0}
html,body{width:1200px;height:3719px;overflow:hidden}
body{position:relative;background:var(--grey-bg);font-family:"Arimo",Arial,sans-serif;color:var(--text)}
.abs{position:absolute}
.brand-name{font-family:"Raleway",sans-serif;font-weight:600;color:var(--green);letter-spacing:1px}
.logo-dot{display:inline-block;border-radius:50%;border:6px solid var(--black);background:var(--white);vertical-align:middle}

/* hero */
.hero{position:absolute;left:0;top:0;width:1200px;height:675px;
  background:linear-gradient(180deg,#8c9296 0%,#b7bcbd 35%,#6f8a5e 65%,#dadbd8 100%)}
.hero-phone{position:absolute;right:76px;top:32px;color:var(--white);font-size:25px;display:flex;align-items:center;gap:14px}
.hero-logo{position:absolute;left:0;width:1200px;top:190px;text-align:center}
.hero-logo .brand-name{font-size:74px;vertical-align:middle;margin-left:20px}
.hero-logo .logo-dot{width:110px;height:110px}
.hero-sub{font-family:"Raleway",sans-serif;font-size:22px;color:#eeeeee;letter-spacing:1px;display:block;margin-top:-10px;padding-left:130px}
.hero-tagline{position:absolute;top:380px;width:1200px;text-align:center;color:var(--white);font-family:"Raleway",sans-serif;font-size:34px;font-weight:500}
.btn{display:inline-block;background:var(--green);color:var(--white);font-family:"Raleway",sans-serif;border-radius:40px;text-align:center}
.hero-cta{position:absolute;left:481px;top:462px;width:238px;height:64px;line-height:64px;font-size:22px}

/* nav */
.nav{position:absolute;top:675px;left:0;width:1200px;height:70px;background:var(--black);border-top:3px solid var(--green)}
.nav a{position:absolute;top:0;height:67px;line-height:67px;color:var(--white);font-family:"Raleway",sans-serif;font-size:18px;text-decoration:none;text-align:center;font-weight:500}
.nav a.active{color:var(--green);border-bottom:3px solid var(--green)}
.nav-badge{position:absolute;left:545px;top:-23px;width:110px;height:110px;border-radius:50%;background:var(--white);border:5px solid var(--green);display:flex;align-items:center;justify-content:center}
.nav-badge span{width:62px;height:62px;border-radius:50%;border:6px solid var(--black)}

/* welcome */
.welcome h1{position:absolute;left:78px;top:795px;font-family:"Raleway",sans-serif;font-weight:500;font-size:46px;color:var(--ink)}
.welcome h1 b{color:var(--green);font-weight:700}
.welcome-copy{position:absolute;left:80px;top:868px;width:650px}
.welcome-copy p{font-size:14px;line-height:23px;color:#777;margin-bottom:12px}
.welcome-photo{position:absolute;left:765px;top:795px;width:330px;height:330px;border-radius:50%;border:14px solid #cfcfcf;
  background:linear-gradient(170deg,#5f9bd0 0%,#9cc0d8 35%,#b97a4a 50%,#6f8e4a 75%,#3f5e2d 100%)}

/* services */
.services-bg{position:absolute;top:1140px;left:0;width:1200px;height:690px;
  background:linear-gradient(180deg,#3a3d39 0%,#2b2e2a 50%,#1f211f 100%)}
.section-badge{position:absolute;width:84px;height:84px;border-radius:50%;background:var(--white);border:4px solid var(--green);display:flex;align-items:center;justify-content:center}
.section-badge span{width:48px;height:48px;border-radius:50%;border:5px solid var(--black)}
.services h2{position:absolute;top:1290px;width:1200px;text-align:center;font-family:"Raleway",sans-serif;font-size:44px;font-weight:500;color:var(--white)}
.services h2 b{color:var(--green);font-weight:700}
.service{position:absolute;width:300px;text-align:center}
.service .ring{margin:0 auto;width:200px;height:200px;border-radius:50%;background:rgba(255,255,255,.1);display:flex;align-items:center;justify-content:center}
.service .disc{width:156px;height:156px;border-radius:50%;background:var(--white);border:6px solid #3a3a3a;display:flex;align-items:center;justify-content:center}
.service.dark .disc{background:#121212;border-color:#121212}
.service.light .disc{background:#eef2ec;border-color:#cfd8ca}
.service .label{margin-top:4px;font-family:"Raleway",sans-serif;font-size:20px;color:var(--white);font-weight:500;white-space:nowrap}
.dome{position:absolute;left:360px;top:1590px;width:483px;height:480px;border-radius:50%;background:var(--white);border:10px solid #e3e3e3;text-align:center;padding-top:90px}
.dome .logo-dot{width:90px;height:90px}
.dome .brand-name{font-size:54px;vertical-align:middle;margin-left:12px}

/* testimonials */
.reviews{position:absolute;top:1830px;left:0;width:1200px;height:480px;background:var(--black)}
.reviews h2{position:absolute;top:58px;width:1200px;text-align:center;font-family:"Raleway",sans-serif;font-size:44px;font-weight:500;color:var(--white)}
.reviews h2 b{color:var(--green);font-weight:700}
.quote-mark{position:absolute;top:130px;width:1200px;text-align:center;color:var(--green);font-family:"Raleway",sans-serif;font-size:90px;font-weight:700;line-height:1}
.reviews blockquote{position:absolute;top:205px;left:110px;width:980px;text-align:center;color:#e6e6e6;font-size:16px;line-height:34px}
.client{position:absolute;top:282px;width:1200px;text-align:center;color:var(--green);font-family:"Raleway",sans-serif;font-size:17px;letter-spacing:1px}
.dots{position:absolute;top:318px;width:1200px;display:flex;justify-content:center;gap:10px}
.dots i{width:14px;height:14px;border-radius:50%;background:var(--white)}
.dots i.on{background:var(--green)}

/* products */
.section-title{position:absolute;width:1200px;text-align:center;font-family:"Raleway",sans-serif;font-size:46px;font-weight:500;color:var(--ink)}
.section-title b{color:var(--green);font-weight:700}
.section-lead{position:absolute;left:180px;width:840px;text-align:center;font-size:15px;line-height:30px;color:#555}
.product{position:absolute;top:2405px;width:250px;text-align:center}
.product .photo{height:188px}
.product h3{margin-top:22px;font-family:"Raleway",sans-serif;font-size:22px;font-weight:500;color:var(--ink)}
.product p{margin-top:8px;font-size:14.5px;line-height:22px;color:#888}
.product svg{margin-top:6px}
.divider{position:absolute;left:77px;top:2800px;width:1046px;height:1px;background:var(--line)}

/* contact */
.field{position:absolute;height:46px;background:var(--white);border:1px solid #d8d8d8;border-radius:4px;font-size:14px;color:#999;padding:14px 12px}
.submit{position:absolute;left:77px;top:3200px;width:548px;height:57px;line-height:57px;font-size:21px;border-radius:30px}
.info{position:absolute;left:680px;font-size:15px}
.info .row{position:absolute;left:0;display:flex;width:440px}
.info .k{width:140px;flex:none;color:var(--green);display:flex;gap:12px;align-items:center;align-self:flex-start;height:26px}
.info .v{color:#444;line-height:26px}
.partners{position:absolute;left:688px;top:3215px;display:flex;gap:24px;align-items:center}
.partners span{font-family:"Arimo",sans-serif;font-weight:700;font-size:24px;color:#2a2a2a;letter-spacing:1px}
.partners span.blue{color:#1f5fa8}

/* footer */
.footer{position:absolute;left:0;top:3260px;width:1200px;height:459px}
.footer-logo{position:absolute;left:545px;top:3352px;width:110px;height:110px;border-radius:50%;border:8px solid var(--green);background:#1d1d1d}
.copyright{position:absolute;top:3566px;width:1200px;text-align:center;font-size:14px;color:#aaa}
.copyright b{color:var(--green);font-weight:400}
.socials{position:absolute;top:3608px;left:504px;display:flex;gap:22px}
.socials i{width:52px;height:52px;border-radius:50%;border:2px solid #444}
.socials i.on{border-color:var(--green);background:#1e2a18}
</style>
</head>
<body>

<section class="hero" role="img" aria-label="Bright sunroom with tall windows, white sofa and garden trees beyond">
  <div class="hero-phone">
    <svg width="34" height="34" viewBox="0 0 34 34"><circle cx="17" cy="17" r="15" fill="none" stroke="#6cc04a" stroke-width="2.5"/><path d="M11 10c1-1 2-1 3 0l2 3c.5.8.3 1.6-.3 2.2l-1 1c.9 1.8 2.2 3.1 4 4l1-1c.6-.6 1.4-.8 2.2-.3l3 2c1 1 1 2 0 3-2 2-5 2-9-2s-5-8-4.9-11.9z" fill="#6cc04a"/></svg>
    555-0142-7730
  </div>
  <div class="hero-logo">
    <span class="logo-dot"></span><span class="brand-name">Velmarix</span>
    <span class="hero-sub">Window Treatment Solutions</span>
  </div>
  <div class="hero-tagline">Specializing in Motorized systems for Indoors and Outdoors</div>
  <a class="btn hero-cta">CONTACT US NOW</a>
</section>

<nav class="nav">
  <a class="active" style="left:149px;width:109px">HOME</a>
  <a style="left:270px;width:100px">ABOUT</a>
  <a style="left:390px;width:120px">SERVICES</a>
  <div class="nav-badge"><span></span></div>
  <a style="left:695px;width:130px">PRODUCTS</a>
  <a style="left:845px;width:110px">GALLERY</a>
  <a style="left:975px;width:110px">CONTACT</a>
</nav>

<section class="welcome">
  <h1>Welcome to <b>Velmarix</b></h1>
  <div class="welcome-copy">
    <p>At Velmarix we specialize in custom high quality window treatments. Whether it is for a condo, home or entire building, we provide free sampling, free on site consultation and turnkey installation services to Toronto, the entire GTA and northern cottage community. We bring over 15 years of expertise serving the design, A/V integrator, builder and architect community, delivering personal attention to every project.</p>
    <p>Offering industry leading manufacturers such as Dimbrell, we provide top-of-the-line motorized and manual products including blinds, drapes, exterior shades, awnings and bug screens. We carry our own economical product line manufactured in the GTA for budget focused or commercial applications.</p>
  </div>
  <div class="welcome-photo" role="img" aria-label="Retractable awning over a terrace overlooking a lake and hills"></div>
</section>

<section class="services">
  <div class="services-bg" role="img" aria-label="Dark toned photo of trees and a garden terrace"></div>
  <svg class="abs" style="left:0;top:1120px" width="1200" height="120" viewBox="0 0 1200 120"><path d="M0 20 Q600 190 1200 20 L1200 0 L0 0Z" fill="#ececec"/></svg>
  <div class="section-badge" style="left:558px;top:1178px"><span></span></div>
  <h2>Our <b>Services</b></h2>

  <div class="service" style="left:316px;top:1363px">
    <div class="ring"><div class="disc">
      <svg width="80" height="80" viewBox="0 0 80 80" fill="none" stroke="#6cc04a" stroke-width="5"><path d="M8 10h64M16 10v62M64 10v62M16 10c6 20 6 40 0 62M64 10c-6 20-6 40 0 62M28 12v58M52 12v58"/></svg>
    </div></div>
    <div class="label">DRAPERY</div>
  </div>
  <div class="service" style="left:577px;top:1363px">
    <div class="ring"><div class="disc">
      <svg width="86" height="80" viewBox="0 0 86 80" fill="none" stroke="#6cc04a" stroke-width="5"><path d="M6 22L14 6h58l8 16zM6 22c0 6 9 6 9 0 0 6 10 6 10 0 0 6 10 6 10 0 0 6 10 6 10 0 0 6 10 6 10 0 0 6 10 6 10 0 0 6 9 6 9 0M12 30v44h62V30M26 74V44h34v30"/></svg>
    </div></div>
    <div class="label">AWNINGS</div>
  </div>
  <div class="service dark" style="left:110px;top:1550px">
    <div class="ring"><div class="disc">
      <svg width="80" height="80" viewBox="0 0 80 80" fill="none" stroke="#6cc04a" stroke-width="5"><rect x="8" y="8" width="64" height="64"/><path d="M8 22h64M8 36h64M8 50h64M24 36v14M40 36v14M56 36v14"/></svg>
    </div></div>
    <div class="label">ROLLER SHADES</div>
  </div>
  <div class="service light" style="left:802px;top:1550px">
    <div class="ring"><div class="disc">
      <svg width="80" height="80" viewBox="0 0 80 80" fill="none" stroke="#6cc04a" stroke-width="5"><rect x="10" y="12" width="60" height="58"/><path d="M10 40h60M40 12v28M6 70h68"/></svg>
    </div></div>
    <div class="label">OUTDOOR BUG SCREENS</div>
  </div>

  <div class="dome">
    <span class="logo-dot"></span><span class="brand-name">Velmarix</span>
  </div>
</section>

<section class="reviews">
  <h2>What Our <b>Client Say</b></h2>
  <div class="quote-mark">&ldquo;</div>
  <blockquote>"Lorem Ipsum is simply dummy text of the printing and typesetting industry. Lorem Ipsum has been the industry's standard dummy text ever since the 1500s, when an unknown printer took a galley of type and scrambled it to make a"</blockquote>
  <div class="client">— CLIENT NAME</div>
  <div class="dots"><i></i><i></i><i class="on"></i><i></i></div>
</section>
<svg class="abs" style="left:0;top:2180px" width="1200" height="140" viewBox="0 0 1200 140"><path d="M0 140 L0 110 Q600 -40 1200 110 L1200 140Z" fill="#ececec"/></svg>

<section class="products">
  <h2 class="section-title" style="top:2268px">Our <b>Product</b></h2>
  <p class="section-lead" style="top:2330px">Lorem Ipsum is simply dummy text of the printing and typesetting industry. Lorem Ipsum has been the industry's standard dummy text ever since the 1500s, when an unknown printer took a</p>

  <div class="product" style="left:77px">
    <div class="photo" role="img" aria-label="Sunroom with roller shades on large windows" style="background:linear-gradient(180deg,#c9ccc9 0%,#9fb0a4 50%,#6f8a6b 100%)"></div>
    <h3>Roller shades</h3>
    <p>Lorem Ipsum is simply dummy text of the printing &amp; typesetting industry. Lorem Ipsum has.</p>
    <svg width="18" height="14" viewBox="0 0 18 14" fill="none" stroke="#6cc04a" stroke-width="2"><path d="M3 2l6 5 6-5M3 7l6 5 6-5"/></svg>
  </div>
  <div class="product" style="left:342px">
    <div class="photo" role="img" aria-label="Patio dining set behind outdoor bug screens" style="background:linear-gradient(180deg,#3a3f3a 0%,#7a9a6a 55%,#4a5a40 100%)"></div>
    <h3>Outdoor Bug Screens</h3>
    <p>Lorem Ipsum is simply dummy text of the printing &amp; typesetting industry. Lorem Ipsum has.</p>
    <svg width="18" height="14" viewBox="0 0 18 14" fill="none" stroke="#6cc04a" stroke-width="2"><path d="M3 2l6 5 6-5M3 7l6 5 6-5"/></svg>
  </div>
  <div class="product" style="left:607px">
    <div class="photo" role="img" aria-label="White outdoor drapes under an awning by a garden" style="background:linear-gradient(180deg,#6f8f5a 0%,#a9c08f 45%,#e2e6e0 100%)"></div>
    <h3>Awnings</h3>
    <p>Lorem Ipsum is simply dummy text of the printing &amp; typesetting industry. Lorem Ipsum has.</p>
    <svg width="18" height="14" viewBox="0 0 18 14" fill="none" stroke="#6cc04a" stroke-width="2"><path d="M3 2l6 5 6-5M3 7l6 5 6-5"/></svg>
  </div>
  <div class="product" style="left:873px">
    <div class="photo" role="img" aria-label="Bright doorway with a pergola screen system" style="background:linear-gradient(180deg,#f0f0ee 0%,#d9dcd6 50%,#b9bdb5 100%)"></div>
    <h3>Outdoor Pergolas</h3>
    <p>Lorem Ipsum is simply dummy text of the printing &amp; typesetting industry. Lorem Ipsum has.</p>
    <svg width="18" height="14" viewBox="0 0 18 14" fill="none" stroke="#6cc04a" stroke-width="2"><path d="M3 2l6 5 6-5M3 7l6 5 6-5"/></svg>
  </div>
  <div class="divider"></div>
</section>

<section class="contact">
  <h2 class="section-title" style="top:2836px">Contact <b>Us</b></h2>
  <p class="section-lead" style="top:2898px">Lorem Ipsum is simply dummy text of the printing and typesetting industry. Lorem Ipsum has been the industry's standard dummy text ever since the 1500s, when an unknown printer took a</p>

  <div class="field" style="left:77px;top:2975px;width:270px">Name*</div>
  <div class="field" style="left:355px;top:2975px;width:270px">Email*</div>
  <div class="field" style="left:77px;top:3028px;width:270px">Phone*</div>
  <div class="field" style="left:355px;top:3028px;width:270px">Product*
    <svg class="abs" style="right:14px;top:19px" width="14" height="8" viewBox="0 0 14 8"><path d="M0 0h14L7 8z" fill="#777"/></svg>
  </div>
  <div class="field" style="left:77px;top:3081px;width:548px;height:110px">Message*</div>
  <a class="btn submit">SUBMIT</a>

  <div class="info" style="top:2985px">
    <div class="row" style="top:0">
      <div class="k"><svg width="16" height="22" viewBox="0 0 16 22"><path d="M8 0C3.6 0 0 3.5 0 7.8 0 13.6 8 22 8 22s8-8.4 8-14.2C16 3.5 12.4 0 8 0zm0 11a3 3 0 110-6 3 3 0 010 6z" fill="#6cc04a"/></svg>Address :</div>
      <div class="v">Velmarix<br>27B-4 Alderwick Rd, Toronto, ON,<br>M5R 2K8</div>
    </div>
    <div class="row" style="top:92px">
      <div class="k"><svg width="20" height="20" viewBox="0 0 20 20"><path d="M4 1c1-1 2-1 3 0l2 3c.5.8.3 1.6-.3 2.2l-1 1c.9 1.8 2.2 3.1 4 4l1-1c.6-.6 1.4-.8 2.2-.3l3 2c1 1 1 2 0 3-2 2-5 2-9-2S2 4 4 1z" fill="#6cc04a"/></svg>Call Us :</div>
      <div class="v">555-0142-7730</div>
    </div>
    <div class="row" style="top:133px">
      <div class="k"><svg width="20" height="16" viewBox="0 0 20 16"><rect width="20" height="16" rx="2" fill="#6cc04a"/><path d="M1 2l9 7 9-7" fill="none" stroke="#fff" stroke-width="2"/></svg>Email Us :</div>
      <div class="v">info@velmarix.com</div>
    </div>
    <div class="row" style="top:174px">
      <div class="k"><svg width="20" height="20" viewBox="0 0 20 20"><circle cx="10" cy="10" r="10" fill="#6cc04a"/><path d="M0 10h20M10 0c-4 5-4 15 0 20M10 0c4 5 4 15 0 20" fill="none" stroke="#fff" stroke-width="1.5"/></svg>Web :</div>
      <div class="v">www.velmarix.ca</div>
    </div>
  </div>
  <div class="partners"><span>DIMBRELL</span><span class="blue">KRAVENHOLT</span></div>
</section>

<footer>
  <svg class="footer abs" viewBox="0 0 1200 459" width="1200" height="459">
    <path d="M0 0 Q600 90 1200 0 L1200 459 L0 459Z" fill="#141414"/>
    <path d="M0 0 Q600 90 1200 0" fill="none" stroke="#6cc04a" stroke-width="4"/>
  </svg>
  <div class="footer-logo"></div>
  <p class="copyright"><b>©Velmarix Window Treatment Solution</b> - 2016. All Rights Reserved</p>
  <div class="socials"><i></i><i class="on"></i><i></i></div>
</footer>

</body>
</html>
```